Storm Restoration Contractor needs a professional letterhead design

Looking for a professional letterhead design. Not looking for your cheapo MS Word standard ones that are readily available. Dont want it to be cookie cutter look like ones readily available online. We just recently changed our logo and want to freshen up all our documents. Our company handles restoring a property back to a pre-loss condition after a storm damages it. For example, wind, hail, flood, fire losses.

Target Market(s)

Property Owners, Homeowners, Property Owners, Commercial Property Owners, Property Management Companies

Industry/Entity Type

Construction Company

Requirements
Must have
• Professional, Use 1 of 2 logo options
• Storm Restoration, Roofing, Siding, Windows

```html
<!DOCTYPE html>
<html lang="en">
<head>
<meta charset="utf-8">
<title>Stormline Exteriors Letterhead</title>
<link rel="stylesheet" href="https://fonts.googleapis.com/css2?family=Didact+Gothic&family=Montserrat:wght@600&display=swap">
<style>
  :root {
    --backdrop: #e4e4e4;
    --paper: #f1f1f1;
    --brand-blue: #2a6aad;
    --brand-grey: #555555;
    --ink: #444444;
    --rule: #9a9a9a;
  }
  * { margin: 0; padding: 0; box-sizing: border-box; }
  html, body {
    width: 1200px;
    height: 1041px;
    overflow: hidden;
    background: var(--backdrop);
  }
  .letterhead {
    position: absolute;
    left: 212px;
    top: 20px;
    width: 800px;
    height: 1033px;
    transform: scale(0.97);
    transform-origin: top left;
    background: var(--paper);
    box-shadow: 0 2px 6px rgba(0,0,0,0.25);
    font-family: "Didact Gothic", sans-serif;
    color: var(--ink);
  }
  .edge-curves {
    position: absolute;
    inset: 0;
    width: 100%;
    height: 100%;
  }
  .edge-curve--left { fill: var(--brand-blue); }
  .edge-curve--right { fill: var(--brand-grey); }

  .brand {
    position: absolute;
    top: 76px;
    left: 0;
    width: 100%;
    display: flex;
    justify-content: center;
    align-items: center;
    gap: 14px;
  }
  .brand__dot {
    width: 56px;
    height: 56px;
    border-radius: 50%;
    background: var(--brand-blue);
  }
  .brand__name {
    font-family: "Montserrat", sans-serif;
    font-weight: 600;
    color: var(--brand-blue);
    font-size: 22px;
    line-height: 24px;
    letter-spacing: 1px;
  }

  .footer {
    position: absolute;
    left: 0;
    width: 100%;
    top: 948px;
    text-align: center;
  }
  .footer__name {
    font-family: "Montserrat", sans-serif;
    font-weight: 600;
    font-size: 10px;
    color: var(--brand-blue);
    letter-spacing: 0.2px;
  }
  .footer__rule {
    width: 320px;
    height: 1px;
    background: var(--rule);
    margin: 6px auto 10px;
  }
  .footer__line {
    font-size: 10.5px;
    line-height: 15px;
  }
  .footer__label { color: var(--brand-blue); font-weight: bold; }
  .footer__web-accent { color: var(--brand-blue); font-weight: bold; }
</style>
</head>
<body>
  <main class="letterhead">
    <svg class="edge-curves" viewBox="0 0 800 1033" preserveAspectRatio="none" aria-hidden="true">
      <path class="edge-curve--left" d="M0,235 Q34,518 0,802 Z"/>
      <path class="edge-curve--right" d="M800,247 Q770,520 800,787 Z"/>
    </svg>

    <header class="brand">
      <span class="brand__dot"></span>
      <div class="brand__name">STORMLINE<br>EXTERIORS</div>
    </header>

    <footer class="footer">
      <div class="footer__name">STORMLINE EXTERIORS</div>
      <div class="footer__rule"></div>
      <p class="footer__line">4120 N Canyon Ridge Road STE 210, Mesa, AZ 85201</p>
      <p class="footer__line">
        <span class="footer__label">T:</span> 480-555-0142 ·
        <span class="footer__label">F:</span> 480-555-0142 ·
        <span class="footer__label">E:</span> info@stormlinext.com ·
        www.<span class="footer__web-accent">stormlinext</span>.com
      </p>
    </footer>
  </main>
</body>
</html>
```